Holistic Health Coach needs a catchy and creative flyer

I need an eye-catching and convincing DL sized flyer for my new health coaching business. I provide advice and regular coaching to people on health, fitness and lifestyle issues.

I want these flyers to create awareness of my business as well as providing some information about what I do and the services that I can provide. I also want the flyers to have a strong and clear call-to-action so they can contact me.

I have provided some photos myself to be used in the flyer if necessary. I have also provided my logo. My Business name is called "Bright Path Notes" however I want to market myself as a " Qualified Holistic Health Coach".

Target Market(s)

Men and Women of all ages who are trying to improve their health and fitness

Industry/Entity Type

Health And Wellness

Font styles to use
Sans Serif

Requirements
Must have
• My Business is called "Bright Path Notes" (as seen in attached logo) but I would like the main marketing message of the flyer to be focused as " Qualified Holistic Health Coach" .
• The Flyer should be DL size.
• Strong call to action
• Catchy and memorable design- as I am a new business I want this to capture people's attention.
• Please see attached document for page content.
Nice to have
• I have also included some recent pictures of myself to be incorporated in the flyer, if appropriate.

```html
<!DOCTYPE html>
<html lang="en">
<head>
<meta charset="utf-8">
<title>Bright Path Notes – Holistic Health Coach Flyer</title>
<link rel="stylesheet" href="https://fonts.googleapis.com/css2?family=Amatic+SC:wght@700&family=Lato:wght@400;700;900&display=swap">
<style>
  :root{
    --page-bg:#ececea;
    --paper-light:#f1f1f0;
    --paper-mid:#dadad9;
    --ink:#1d1d1d;
    --ink-soft:#333333;
    --green:#5ba12b;
    --green-bright:#8cc63f;
    --tick-red:#d7262f;
    --band-black:#1a1a1a;
    --white:#ffffff;
    --navy:#27303d;
  }
  *{box-sizing:border-box;margin:0;padding:0}
  html,body{width:1200px;height:1149px;overflow:hidden;background:var(--page-bg)}
  body{position:relative;font-family:"Lato",Arial,sans-serif;color:var(--ink)}

  .flyer{
    position:absolute;top:74px;width:520px;height:1000px;overflow:hidden;
    background:radial-gradient(ellipse at 45% 40%,var(--paper-light) 0%,var(--paper-mid) 100%);
    box-shadow:0 6px 18px rgba(0,0,0,.22);
  }
  .flyer--front{left:60px}
  .flyer--back{left:620px}

  .hand{font-family:"Amatic SC","Arial Narrow",sans-serif;font-weight:700;text-transform:uppercase;line-height:.94}
  .green{color:var(--green)}

  /* Front */
  .topic-band{
    position:absolute;left:0;top:0;width:100%;height:46px;background:var(--band-black);
    color:var(--white);font-weight:900;font-size:21px;letter-spacing:2.5px;
    display:flex;align-items:center;justify-content:center;gap:12px;
  }
  .topic-band .accent{color:var(--green-bright)}
  .topic-band .divider{font-weight:400;opacity:.8}

  .photo-food{
    position:absolute;left:0;top:46px;width:175px;height:640px;
    background:
      radial-gradient(circle at 70% 70%,#7fb843 0 38px,transparent 40px),
      radial-gradient(circle at 30% 76%,#86bd45 0 36px,transparent 38px),
      linear-gradient(170deg,#f2f2f0 0%,#e9e9e7 16%,#a6d05e 32%,#c9d9b3 48%,#9cc85a 58%,#dfe3e4 82%,#cfd8d6 100%);
    -webkit-mask-image:linear-gradient(90deg,#000 70%,transparent 100%);
    mask-image:linear-gradient(90deg,#000 70%,transparent 100%);
  }
  .headline{
    position:absolute;left:196px;top:72px;width:310px;text-align:center;font-size:76px;
  }
  .photo-coach{
    position:absolute;left:290px;top:520px;width:230px;height:480px;
    background:linear-gradient(180deg,#b99a80 0%,#c7ab92 18%,#f3f3f1 30%,#fafaf8 76%,var(--navy) 82%,var(--navy) 100%);
    border-radius:110px 0 0 0;
    -webkit-mask-image:linear-gradient(90deg,transparent 0%,#000 14%);
    mask-image:linear-gradient(90deg,transparent 0%,#000 14%);
  }
  .coach-quote{position:absolute;left:24px;top:744px;width:270px;font-size:46px}
  .coach-name{position:absolute;left:30px;top:896px;width:250px;text-align:center;font-weight:900;font-size:22px}
  .coach-credentials{position:absolute;left:30px;top:926px;width:250px;text-align:center;font-size:12px;line-height:1.35;color:var(--ink-soft)}

  /* Back */
  .photo-apples{
    position:absolute;left:330px;top:0;width:190px;height:230px;
    background:
      radial-gradient(circle at 30% 22%,#6fae2e 0 40px,transparent 42px),
      radial-gradient(circle at 74% 32%,#78b635 0 42px,transparent 44px),
      radial-gradient(ellipse at 70% 80%,rgba(200,214,220,.9) 0 48px,transparent 70px);
    -webkit-mask-image:linear-gradient(90deg,transparent 0%,#000 30%);
    mask-image:linear-gradient(90deg,transparent 0%,#000 30%);
  }
  .focus-list{position:absolute;left:58px;top:50px;list-style:none}
  .focus-list li{display:flex;align-items:center;gap:12px;font-weight:700;font-size:20px;height:30px;color:var(--ink-soft)}
  .focus-list svg{width:22px;height:22px;flex:none}

  .services{position:absolute;left:118px;top:236px;width:340px}
  .services h2{font-size:20px;font-weight:900;color:var(--green);margin-bottom:4px}
  .services ul{padding-left:18px;font-size:14.5px;line-height:20.5px;color:var(--ink-soft)}

  .cta{position:absolute;left:0;top:522px;width:100%;text-align:center;font-size:82px}
  .contact{position:absolute;left:0;top:630px;width:100%;text-align:center;font-size:20px;line-height:29px;color:var(--ink-soft)}
  .contact b{color:var(--green);font-weight:900}
  .note{position:absolute;left:0;top:772px;width:100%;text-align:center;font-size:13px;color:var(--ink-soft)}

  .footer-band{
    position:absolute;left:0;bottom:0;width:100%;height:190px;background:var(--band-black);
    display:flex;flex-direction:column;align-items:center;justify-content:center;gap:26px;
  }
  .brand{display:flex;align-items:center;gap:12px;color:var(--white);font-weight:900;font-size:26px;letter-spacing:1px}
  .brand-dot{width:38px;height:38px;border-radius:50%;background:var(--green-bright)}
  .website{color:var(--white);font-size:21px;letter-spacing:.5px}
</style>
</head>
<body>

<section class="flyer flyer--front" aria-label="Flyer front">
  <div class="topic-band"><span>Health</span><span class="divider">|</span><span class="accent">Nutrition</span><span class="divider">|</span><span>Lifestyle</span></div>
  <div class="photo-food" role="img" aria-label="Photo of sneakers, a lunch box with healthy food, a tape measure, green apples and a water bottle"></div>
  <h1 class="headline hand">"Be your<br>best through<br><span class="green">food and<br>lifestyle</span><br>changes."</h1>
  <div class="photo-coach" role="img" aria-label="Photo of the health coach standing with arms folded, wearing a white top"></div>
  <p class="coach-quote hand">"I can help, I'm a qualified holistic <span class="green">health coach."</span></p>
  <p class="coach-name">— Clara Dunmore</p>
  <p class="coach-credentials">BA in Sport and<br>Exercise Management,<br>M Pharmacy</p>
</section>

<section class="flyer flyer--back" aria-label="Flyer back">
  <div class="photo-apples" role="img" aria-label="Photo of green apples and a water bottle"></div>
  <ul class="focus-list">
    <li><svg viewBox="0 0 22 22"><rect x="1.5" y="4.5" width="15" height="15" fill="none" stroke="#555" stroke-width="1.6"/><path d="M5 11 L9 16 L20 3" fill="none" stroke="var(--tick-red)" stroke-width="3" stroke-linecap="round" stroke-linejoin="round"/></svg>Nutritional Advice</li>
    <li><svg viewBox="0 0 22 22"><rect x="1.5" y="4.5" width="15" height="15" fill="none" stroke="#555" stroke-width="1.6"/><path d="M5 11 L9 16 L20 3" fill="none" stroke="var(--tick-red)" stroke-width="3" stroke-linecap="round" stroke-linejoin="round"/></svg>Fitness Planning</li>
    <li><svg viewBox="0 0 22 22"><rect x="1.5" y="4.5" width="15" height="15" fill="none" stroke="#555" stroke-width="1.6"/><path d="M5 11 L9 16 L20 3" fill="none" stroke="var(--tick-red)" stroke-width="3" stroke-linecap="round" stroke-linejoin="round"/></svg>Natural Health Management</li>
    <li><svg viewBox="0 0 22 22"><rect x="1.5" y="4.5" width="15" height="15" fill="none" stroke="#555" stroke-width="1.6"/><path d="M5 11 L9 16 L20 3" fill="none" stroke="var(--tick-red)" stroke-width="3" stroke-linecap="round" stroke-linejoin="round"/></svg>Lifestyle Assessment</li>
  </ul>

  <div class="services">
    <h2>My services:</h2>
    <ul>
      <li>Holistic Health Check-up</li>
      <li>Weight-loss goals</li>
      <li>Mini Medication Reviews</li>
      <li>Review of Vitamins and Supplements</li>
      <li>Nutritional Guidance</li>
      <li>Exercise Guidance</li>
      <li>Use of Natural Therapies</li>
      <li>Sleep Management</li>
      <li>Stress Management</li>
      <li>Specific Health Concerns</li>
      <li>Long Term Disease Management</li>
      <li>Food Tips and Education</li>
    </ul>
  </div>

  <h2 class="cta hand">Get started now!</h2>
  <p class="contact">
    Contact <b>Clara Dunmore</b><br>
    <b>Phone:</b> (02) 5550 1842<br>
    <b>Mobile:</b> 0400 555 218<br>
    <b>Email:</b> clara@brightpathnotes.com.au
  </p>
  <p class="note">Home consultations available.</p>

  <footer class="footer-band">
    <div class="brand"><span class="brand-dot"></span><span>Bright Path Notes</span></div>
    <div class="website">www.brightpathnotes.com.au</div>
  </footer>
</section>

</body>
</html>
```